Banner Ad Designs for tick and flea products

We sell tick and flea products online and want some great banner designs for our online website to promote our tick and flea products.

The ads must be made up in both Flash and HTML5
Ads can be formatted as .JPEG or .GIF files.

Please see the following url for creative requirements
http://help.bannerkite.com/creative-requirements/

Creative licence no limits to your imagination!

Ads must be created in the following sizes:

- Banner – 468×60
- Square – 250×250
- Small Square – 200×200
- Leaderboard – 728×90
- Medium Rectangle – 300×250
- Chatterly – 100×72

please view our website at www.globalpawstore.com.au or .com to get a feel for our website.

The aim is to attract customers who want to save on tick and flea purchases for their pets (dogs and cats)

Target Market(s)

Anyone who owns a dog or cat

Industry/Entity Type

Online

Font styles to use
Sans Serif
Other font styles liked:
• creative licence on font styles

Requirements
Must have
• Must have a strong urge to entice customers to click through.

Images wording and text etc use creative lic
Nice to have
• Strong appeal to dog and cat owners and how they can save on flea and tick essentials.
Keep it simple but effective.
Be fun and playful and inviting.
Should not have
• Please do not use words like cheap - cheapest

Strobing & Flashing - Strobing, flashing backgrounds, or otherwise distracting ads are not allowed. Do not attempt to overtly distract the user from page content.

```html
<!DOCTYPE html>
<html lang="en">
<head>
<meta charset="utf-8">
<title>Global Paw Store – Banner Set</title>
<link rel="stylesheet" href="https://fonts.googleapis.com/css2?family=Varela+Round&family=PT+Sans+Narrow&family=Arimo:wght@400&display=swap">
<style>
  :root {
    --backdrop: #a3a3a3;
    --promo-green: #8bb83a;
    --promo-green-light: #a3cc52;
    --sky-top: #9dd3ee;
    --sky-mid: #58aee0;
    --sky-bottom: #1f88c4;
    --panel-white: #ffffff;
    --text-white: #ffffff;
    --brand-navy: #1b3a7a;
    --url-blue: #1c2f8c;
    --caption: #333333;
    --photo-warm: #c9a27a;
    --photo-cool: #d9dde0;
  }
  * { margin: 0; padding: 0; box-sizing: border-box; }
  html, body { width: 1200px; height: 900px; overflow: hidden; }
  body { background: var(--backdrop); position: relative; font-family: "PT Sans Narrow", sans-serif; }

  .banner { position: absolute; left: 63px; width: 1092px; height: 134px; overflow: hidden; }
  .banner--tick-flea { top: 33px; background: linear-gradient(180deg, var(--promo-green-light), var(--promo-green)); }
  .banner--promise-a { top: 186px; }
  .banner--promise-b { top: 338px; }
  .banner--save { top: 489px; }
  .banner--web { top: 642px; }

  .brand-panel {
    position: absolute; left: 0; top: 0; width: 285px; height: 100%;
    background: var(--panel-white);
    display: flex; align-items: center; justify-content: center; gap: 12px;
  }
  .brand-dot { width: 22px; height: 22px; border-radius: 50%; background: var(--brand-navy); flex: none; }
  .brand-name { font-family: "PT Sans Narrow", sans-serif; font-size: 34px; color: var(--brand-navy); line-height: 1; }

  .sky {
    position: absolute; left: 285px; top: 0; right: 0; height: 100%;
    background: linear-gradient(180deg, var(--sky-top) 0%, var(--sky-mid) 45%, var(--sky-bottom) 100%);
  }

  .photo { position: absolute; top: 0; height: 100%; }
  .photo--warm { background: linear-gradient(90deg, rgba(255,255,255,0), var(--photo-warm) 35%, var(--photo-cool)); }
  .photo--solid { background: linear-gradient(180deg, var(--photo-cool), var(--photo-warm)); }

  .headline-tick {
    position: absolute; left: 0; right: 0; top: 22px; text-align: center;
    font-family: "Varela Round", sans-serif; color: var(--text-white);
    font-size: 40px; line-height: 46px;
  }
  .promise {
    position: absolute; left: 387px; top: 22px;
    color: var(--text-white); font-size: 35px; line-height: 45px;
  }
  .save-line {
    position: absolute; left: 387px; top: 34px; color: var(--text-white);
    display: flex; align-items: baseline; gap: 16px; white-space: nowrap;
  }
  .save-line__big { font-size: 55px; line-height: 1; }
  .save-line__small { font-size: 26px; position: relative; top: -14px; }
  .web-address {
    position: absolute; left: 545px; top: 50px; font-family: "Arimo", sans-serif;
    color: var(--url-blue); white-space: nowrap; display: flex; align-items: baseline;
  }
  .web-address__small { font-size: 20px; }
  .web-address__main { font-size: 31px; }

  .caption {
    position: absolute; left: 0; right: 0; top: 822px; text-align: center;
    font-family: "Arimo", sans-serif; font-size: 22px; color: var(--caption);
  }
</style>
</head>
<body>

  <section class="banner banner--tick-flea">
    <div class="photo photo--solid" style="left:0;width:162px;" role="img" aria-label="Photo of a small dog and a tabby cat sitting together"></div>
    <p class="headline-tick">Save on genuine brand<br>tick and flea products</p>
    <div class="photo photo--solid" style="left:927px;width:165px;" role="img" aria-label="Photo of three pugs on leads"></div>
  </section>

  <section class="banner banner--promise-a">
    <div class="brand-panel"><span class="brand-dot"></span><span class="brand-name">Global Paw Store</span></div>
    <div class="sky"></div>
    <p class="promise">Our promise to deliver affordable<br>solutions to your pet care needs</p>
    <div class="photo photo--warm" style="left:935px;width:157px;" role="img" aria-label="Photo of a tabby cat lying beside a small dog"></div>
  </section>

  <section class="banner banner--promise-b">
    <div class="brand-panel"><span class="brand-dot"></span><span class="brand-name">Global Paw Store</span></div>
    <div class="sky"></div>
    <p class="promise">Our promise to deliver affordable<br>solutions to your pet care needs</p>
    <div class="photo photo--warm" style="left:837px;width:255px;" role="img" aria-label="Photo of a tabby cat lying beside a small dog"></div>
  </section>

  <section class="banner banner--save">
    <div class="brand-panel"><span class="brand-dot"></span><span class="brand-name">Global Paw Store</span></div>
    <div class="sky"></div>
    <p class="save-line"><span class="save-line__big">Save today</span><span class="save-line__small">and visit our website for more information</span></p>
    <div class="photo photo--warm" style="left:1005px;width:87px;" role="img" aria-label="Photo of a Yorkshire terrier"></div>
  </section>

  <section class="banner banner--web">
    <div class="brand-panel"><span class="brand-dot"></span><span class="brand-name">Global Paw Store</span></div>
    <div class="sky"></div>
    <div class="photo photo--solid" style="left:297px;width:135px;" role="img" aria-label="Photo of a Yorkshire terrier standing"></div>
    <p class="web-address"><span class="web-address__small">www.</span><span class="web-address__main">globalpawstore</span><span class="web-address__small">.com.au</span></p>
  </section>

  <p class="caption">view on exteral link in submition’s description</p>

</body>
</html>
```